Attic Lanterns (Progressive House Album)

Hey Guys,

I'm a music artist and I need a CD Cover done for my new album.The album is called "Attic Lanterns" and I really need something artistic, almost like a painting that reflects the name of the album.

Also please feel free to step out from the whole "almost like a painting" box, if your inner creator has something else to say. But preferably I'd have it as a painting...

Here are some keywords: Deep, Progressive, Lucid Dreaming, Ocean, Bedroom...

Please listen to the 3:30 demo of the album to get a better idea.

Thanks,

ToLa

Update:

I've uploaded a few images to kinda help you with the mood/colour tone and direction of what I want, Also, the script writing (I've uploaded a few examples), do it in white colour (left to right, going little bit upwards), preferably on the bottom of the image, simple, one touch, thin hand writing. Have it fading in size (bigger to smaller) as you get to the end of each word. Just like when you sign something, but have it written in two lines.

The whole image should be deep in colour with sort of a glow effect.

Must have
• Name of the album with Script writing,
Should not have
• No paper mosaic art. Image pieced together with cut outs from different sources.

```html
<!DOCTYPE html>
<html lang="en">
<head>
<meta charset="utf-8">
<title>Attic Lanterns – Album Cover</title>
<link href="https://fonts.googleapis.com/css2?family=Great+Vibes&display=swap" rel="stylesheet">
<style>
  :root {
    --stage: #2a2a2e;
    --navy-deep: #0b0f3a;
    --navy: #1a2268;
    --ocean: #2d8fd6;
    --surface: #3aa8ee;
    --glow: #a8e2ff;
    --nebula: #c83f7c;
    --violet: #5a3f9a;
    --mist: #d8c8e8;
    --script-white: #ffffff;
    --artist-blue: #6a90d0;
  }
  html, body {
    margin: 0;
    width: 1200px;
    height: 751px;
    overflow: hidden;
    background: var(--stage);
  }
  .canvas {
    position: relative;
    width: 1200px;
    height: 751px;
  }
  .cover {
    position: absolute;
    top: 79px;
    width: 552px;
    height: 552px;
    overflow: hidden;
    box-shadow: 0 6px 18px rgba(0,0,0,0.55);
  }
  .cover--front { left: 41px; }
  .cover--back  { left: 614px; }

  .cover__art {
    position: absolute;
    inset: 0;
    box-shadow: inset 0 0 90px rgba(5,6,30,0.85);
    background:
      radial-gradient(ellipse 120px 90px at 70% 30%, rgba(200,235,255,0.55) 0%, transparent 100%),
      radial-gradient(ellipse 300px 90px at 72% 4%, rgba(90,190,245,0.85) 0%, rgba(45,143,214,0.4) 55%, transparent 100%),
      radial-gradient(ellipse 150px 110px at 20% 32%, rgba(200,63,124,0.85) 0%, rgba(150,60,140,0.45) 50%, transparent 100%),
      radial-gradient(ellipse 200px 120px at 35% 10%, rgba(216,200,232,0.55) 0%, transparent 100%),
      radial-gradient(ellipse 220px 160px at 40% 55%, rgba(90,63,154,0.45) 0%, transparent 100%),
      radial-gradient(ellipse 260px 140px at 55% 88%, rgba(70,90,190,0.35) 0%, transparent 100%),
      radial-gradient(ellipse 200px 260px at 78% 50%, rgba(45,143,214,0.3) 0%, transparent 100%),
      linear-gradient(180deg, var(--navy) 0%, var(--navy-deep) 100%);
  }
  .cover--back .cover__art {
    background:
      radial-gradient(ellipse 110px 200px at 66% 52%, rgba(120,210,255,0.75) 0%, rgba(45,143,214,0.45) 55%, transparent 100%),
      radial-gradient(ellipse 260px 260px at 64% 40%, rgba(45,143,214,0.45) 0%, transparent 100%),
      radial-gradient(ellipse 300px 90px at 68% 4%, rgba(90,190,245,0.85) 0%, rgba(45,143,214,0.4) 55%, transparent 100%),
      radial-gradient(ellipse 150px 110px at 18% 34%, rgba(200,63,124,0.85) 0%, rgba(150,60,140,0.45) 50%, transparent 100%),
      radial-gradient(ellipse 200px 120px at 35% 10%, rgba(216,200,232,0.55) 0%, transparent 100%),
      radial-gradient(ellipse 200px 110px at 42% 62%, rgba(90,63,154,0.45) 0%, transparent 100%),
      radial-gradient(ellipse 280px 100px at 55% 82%, rgba(90,80,170,0.35) 0%, transparent 100%),
      linear-gradient(180deg, var(--navy) 0%, var(--navy-deep) 100%);
  }

  .cover__centrepiece {
    position: absolute;
    left: 120px;
    top: 235px;
    width: 330px;
    height: 200px;
    background:
      radial-gradient(ellipse closest-side at 45% 55%, rgba(225,242,255,0.8) 0%, rgba(160,205,245,0.55) 45%, rgba(90,140,220,0.25) 75%, transparent 100%),
      radial-gradient(ellipse closest-side at 78% 30%, rgba(170,225,255,0.45) 0%, transparent 100%);
  }

  .light-flare {
    position: absolute;
    left: 150px;
    top: 385px;
    width: 80px;
    height: 80px;
    background: radial-gradient(circle closest-side, rgba(255,255,255,0.9) 0%, rgba(200,220,255,0.35) 35%, transparent 100%);
  }
  .lens-ring {
    position: absolute;
    left: 40px;
    top: 368px;
    width: 58px;
    height: 58px;
    border-radius: 50%;
    border: 3px solid rgba(210,100,130,0.35);
  }

  .album-title {
    position: absolute;
    margin: 0;
    font-family: "Great Vibes", cursive;
    font-weight: 400;
    color: var(--script-white);
    line-height: 1;
    transform: rotate(-3deg);
    transform-origin: left top;
    text-shadow: 0 0 8px rgba(168,226,255,0.35);
  }
  .album-title__line { display: block; }
  .album-title--large { left: 56px; top: 46px; }
  .album-title--large .album-title__line--first  { font-size: 98px; }
  .album-title--large .album-title__line--second { font-size: 64px; margin-left: 172px; margin-top: -20px; }
  .album-title--small { left: 54px; top: 400px; }
  .album-title--small .album-title__line--first  { font-size: 64px; }
  .album-title--small .album-title__line--second { font-size: 42px; margin-left: 106px; margin-top: -12px; }

  .artist-name {
    position: absolute;
    right: 48px;
    bottom: 30px;
    margin: 0;
    font-family: "Great Vibes", cursive;
    font-size: 54px;
    color: var(--artist-blue);
    line-height: 1;
  }
</style>
</head>
<body>
  <main class="canvas">
    <section class="cover cover--front">
      <div class="cover__art" role="img" aria-label="Painted deep ocean nebula in blue, violet and pink with light from the water surface"></div>
      <div class="cover__centrepiece" role="img" aria-label="Illustrated white bed floating underwater, dissolving into bubbles and spray"></div>
      <h1 class="album-title album-title--large">
        <span class="album-title__line album-title__line--first">Attic</span>
        <span class="album-title__line album-title__line--second">Lanterns</span>
      </h1>
      <p class="artist-name">ToLa</p>
    </section>

    <section class="cover cover--back">
      <div class="cover__art" role="img" aria-label="Painted deep ocean nebula with a shaft of bright blue light from above"></div>
      <div class="lens-ring"></div>
      <div class="light-flare"></div>
      <h2 class="album-title album-title--small">
        <span class="album-title__line album-title__line--first">Attic</span>
        <span class="album-title__line album-title__line--second">Lanterns</span>
      </h2>
    </section>
  </main>
</body>
</html>
```